Unique Business Card Design

Unique Business Card design for our orthotic and prosthetic company. Our logo is on our website, color is light blue. Unique shape (artificial leg shaped, vertical, etc..) preferred. Logo, business name, individual name and basic demographics needed.

Industry/Entity Type

Business

Contact Information for Business Card

Logo, Industry, Phone # Logo, "Prosthetic & Orthotic Services" Place to add individual name and contact info

Colors
cee9f5

Requirements
Must have
• The icon must be there, placement of "Prosthetic & Orthotic Services" can be moved
Nice to have
• Like the mix of light blue, and a little darker blue. One design included the icons from my website which was a nice touch

```html
<!DOCTYPE html>
<html lang="en">
<head>
<meta charset="utf-8">
<title>Limbwell Inc. – Business Card</title>
<link href="https://fonts.googleapis.com/css2?family=Montserrat:wght@400;600;700&family=Cormorant+Garamond:ital,wght@1,500&display=swap" rel="stylesheet">
<style>
  :root {
    --brand-blue: #1c63b4;
    --brand-blue-dark: #16539a;
    --light-blue: #cee9f5;
    --icon-blue: #a9cdee;
    --white: #ffffff;
    --backdrop: #2b2b2d;
  }
  * { box-sizing: border-box; margin: 0; padding: 0; }
  html, body {
    width: 1200px; height: 900px; overflow: hidden;
    background: var(--backdrop);
    font-family: "Montserrat", Arial, sans-serif;
  }
  .canvas { position: relative; width: 1200px; height: 900px; }
  .card {
    position: absolute; left: 250px; width: 700px; height: 400px;
    border-radius: 26px; overflow: hidden; background: var(--white);
  }
  .card-front { top: 35px; }
  .card-back { top: 465px; }

  /* front */
  .brand {
    position: absolute; left: 95px; top: 70px;
    display: flex; align-items: center; gap: 30px;
  }
  .brand-mark {
    width: 150px; height: 150px; border-radius: 50%;
    background: var(--brand-blue);
  }
  .brand-name {
    font-weight: 700; font-size: 42px; color: var(--brand-blue);
    letter-spacing: 0.5px; line-height: 1;
    padding-bottom: 8px; border-bottom: 3px solid var(--brand-blue);
  }
  .brand-tagline {
    font-family: "Cormorant Garamond", Georgia, serif;
    font-style: italic; font-weight: 500; font-size: 24px;
    color: var(--brand-blue); margin-top: 6px; margin-left: 40px;
  }
  .services {
    position: absolute; left: 80px; right: 80px; bottom: 55px;
    display: flex; justify-content: space-between;
  }
  .service {
    display: flex; flex-direction: column; align-items: center; gap: 12px;
    width: 160px;
  }
  .service-icon {
    width: 62px; height: 62px; border-radius: 50%;
    background: radial-gradient(circle at 35% 30%, var(--light-blue), var(--icon-blue));
    border: 2px solid #d7e9f8;
  }
  .service-label {
    font-weight: 700; font-size: 16px; color: var(--brand-blue);
    letter-spacing: 0.3px;
  }

  /* back */
  .back-art { position: absolute; inset: 0; }
  .contact {
    position: absolute; right: 50px; top: 44px;
    text-align: right; color: var(--white);
  }
  .contact-name { font-weight: 700; font-size: 29px; line-height: 1.1; }
  .contact-title { font-size: 16px; margin-bottom: 10px; }
  .contact-line {
    font-size: 15px; line-height: 1.55;
    display: flex; justify-content: flex-end; align-items: center; gap: 8px;
    white-space: nowrap;
  }
  .contact-line svg { width: 12px; height: 12px; flex: none; }
  .contact-line.plain { padding-right: 20px; }
  .web strong { font-weight: 700; }
</style>
</head>
<body>
<main class="canvas">

  <section class="card card-front">
    <div class="brand">
      <div class="brand-mark"></div>
      <div>
        <div class="brand-name">LIMBWELL INC.</div>
        <div class="brand-tagline">Prosthetic &amp; Orthotic Services</div>
      </div>
    </div>
    <div class="services">
      <div class="service">
        <div class="service-icon" role="img" aria-label="Orthotics icon: foot and ankle brace"></div>
        <div class="service-label">ORTHOTICS</div>
      </div>
      <div class="service">
        <div class="service-icon" role="img" aria-label="Prosthetics icon: standing figure"></div>
        <div class="service-label">PROSTHETICS</div>
      </div>
      <div class="service">
        <div class="service-icon" role="img" aria-label="Vascular icon: wheelchair user"></div>
        <div class="service-label">VASCULAR</div>
      </div>
    </div>
  </section>

  <section class="card card-back">
    <svg class="back-art" viewBox="0 0 700 400" width="700" height="400" aria-hidden="true">
      <rect width="700" height="400" fill="var(--brand-blue)"/>
      <circle cx="-140" cy="460" r="520" fill="var(--white)"/>
      <circle cx="-140" cy="460" r="534" fill="none" stroke="var(--white)" stroke-width="2"/>
      <circle cx="-140" cy="460" r="546" fill="none" stroke="var(--white)" stroke-width="2"/>
      <path d="M700 30 L690 30 Q668 30 668 55 L668 150 Q668 175 690 175 L700 175 Z" fill="var(--white)"/>
      <circle cx="165" cy="255" r="118" fill="var(--brand-blue)"/>
    </svg>
    <div class="contact">
      <div class="contact-name">Mira Kestler</div>
      <div class="contact-title">Orthotist/Prosthetist</div>
      <div class="contact-line plain"><span>820 Harbor Ave.</span></div>
      <div class="contact-line plain"><span>Easton, NY 10000</span></div>
      <div class="contact-line"><span>555-0142318</span>
        <svg viewBox="0 0 12 12"><rect x="3" y="0.5" width="6" height="11" rx="1.2" fill="none" stroke="#fff" stroke-width="1.2"/></svg>
      </div>
      <div class="contact-line"><span>555.014.2700</span>
        <svg viewBox="0 0 12 12"><path d="M2.5 1 L4.5 1 L5.3 3.6 L4 4.7 Q5.2 7.2 7.4 8.1 L8.5 6.8 L11 7.6 L11 9.6 Q10 11 8.5 10.8 Q2 9.5 1 3.2 Q1 1.6 2.5 1 Z" fill="#fff"/></svg>
      </div>
      <div class="contact-line"><span>555.014.2919</span>
        <svg viewBox="0 0 12 12"><rect x="1" y="4" width="10" height="5" rx="1" fill="#fff"/><rect x="3" y="1" width="6" height="3" fill="#fff"/><rect x="3" y="8" width="6" height="3" fill="#fff"/></svg>
      </div>
      <div class="contact-line"><span>mkestler@limbwellinc.com</span>
        <svg viewBox="0 0 12 12"><rect x="1" y="2.5" width="10" height="7" fill="none" stroke="#fff" stroke-width="1.2"/><path d="M1 2.5 L6 6.5 L11 2.5" fill="none" stroke="#fff" stroke-width="1.2"/></svg>
      </div>
      <div class="contact-line web"><span>www.<strong>limbwellinc</strong>.com</span>
        <svg viewBox="0 0 12 12"><circle cx="6" cy="6" r="5" fill="none" stroke="#fff" stroke-width="1.2"/><path d="M1 6 H11 M6 1 Q3 6 6 11 M6 1 Q9 6 6 11" fill="none" stroke="#fff" stroke-width="1"/></svg>
      </div>
    </div>
  </section>

</main>
</body>
</html>
```